BOLD & MINIMALIST DESIGN NEEDED

We want a very bold but minimalistic business card design that is impactful and utilizes both sides of the business card. Our current logo is included for your use.

We want bold fonts and good use of negative space. We don't want the logo to overpower the design.

Target Market(s)

Professionals who are building new commercial buildings.

Industry/Entity Type

Construction

Contact Information for Business Card

Name, Title, email, office phone, cell phone, website

Font styles to use
Serif
Sans Serif

Requirements
Must have
• Bold design!

```html
<!DOCTYPE html>
<html lang="en">
<head>
<meta charset="utf-8">
<title>Ridgeline Build Co — Business Card</title>
<link rel="stylesheet" href="https://fonts.googleapis.com/css2?family=Montserrat:wght@400;500;700;800&display=swap">
<style>
  :root {
    --stage: #2b2b2d;
    --card: #161616;
    --card-edge: #202020;
    --gloss: #3c3c3c;
    --ink: #f2f2f2;
    --accent: #7ac143;
  }
  * { box-sizing: border-box; margin: 0; padding: 0; }
  html, body {
    width: 1200px; height: 874px; overflow: hidden;
    background: var(--stage);
    font-family: "Montserrat", sans-serif;
  }
  .sheet {
    position: relative; width: 1200px; height: 874px;
    display: flex; flex-direction: column; align-items: center; justify-content: center; gap: 36px;
  }
  .card {
    position: relative; width: 680px; height: 388px;
    background: var(--card);
    border-radius: 22px;
    box-shadow: 0 18px 40px rgba(0,0,0,.45), inset 0 0 0 1px var(--card-edge);
    overflow: hidden;
  }

  /* Back side */
  .card--back { display: flex; align-items: center; justify-content: center; }
  .back-mark {
    display: flex; align-items: center; gap: 18px;
    color: var(--gloss); white-space: nowrap;
  }
  .back-mark__square { width: 42px; height: 42px; background: var(--gloss); flex: none; }
  .back-mark__name {
    font-weight: 800; font-size: 40px; letter-spacing: 1px; line-height: 1;
  }

  /* Front side */
  .brand {
    position: absolute; left: 48px; top: 46px;
    display: flex; align-items: center; gap: 10px;
    color: var(--ink); white-space: nowrap;
  }
  .brand__square { width: 22px; height: 22px; background: var(--ink); flex: none; }
  .brand__name { font-weight: 800; font-size: 24px; letter-spacing: .5px; line-height: 1; }

  .address {
    position: absolute; left: 48px; top: 112px;
    color: var(--ink); font-size: 17px; line-height: 1.45; font-weight: 400;
  }
  .contacts {
    position: absolute; left: 48px; top: 190px;
    list-style: none; color: var(--ink); font-size: 17px; line-height: 1;
  }
  .contacts li { display: flex; align-items: center; gap: 10px; margin-bottom: 12px; }
  .contacts svg { width: 14px; height: 14px; fill: var(--accent); flex: none; }

  .person {
    position: absolute; right: 48px; top: 104px; text-align: right; white-space: nowrap;
  }
  .person__name { color: var(--accent); font-weight: 700; font-size: 28px; letter-spacing: 1px; line-height: 1; }
  .person__title { color: var(--ink); font-weight: 500; font-size: 16px; letter-spacing: 1px; margin-top: 10px; }
  .person-bar {
    position: absolute; right: 28px; top: 104px; width: 8px; height: 56px; background: var(--accent);
  }

  .front-block {
    position: absolute; right: 70px; bottom: -30px; width: 230px; height: 200px;
    background: linear-gradient(135deg, #d9d9d9 0%, #6a6a6a 45%, #1c1c1c 100%);
  }
</style>
</head>
<body>
  <main class="sheet">
    <section class="card card--back" aria-label="Card back">
      <div class="back-mark">
        <span class="back-mark__square"></span>
        <span class="back-mark__name">RIDGELINE BUILD CO</span>
      </div>
    </section>

    <section class="card card--front" aria-label="Card front">
      <div class="brand">
        <span class="brand__square"></span>
        <span class="brand__name">RIDGELINE BUILD CO</span>
      </div>

      <p class="address">Your address, City<br>State, Zip 1234</p>

      <ul class="contacts">
        <li><svg viewBox="0 0 16 16"><path d="M3 1h3l1.5 4-2 1.3a9 9 0 0 0 4.2 4.2L11 8.5l4 1.5v3a2 2 0 0 1-2 2A12 12 0 0 1 1 3a2 2 0 0 1 2-2z"/></svg>123 456 789</li>
        <li><svg viewBox="0 0 16 16"><path d="M4 0h8a1 1 0 0 1 1 1v14a1 1 0 0 1-1 1H4a1 1 0 0 1-1-1V1a1 1 0 0 1 1-1zm1 2v10h6V2zm3 11a1 1 0 1 0 0 2 1 1 0 0 0 0-2z"/></svg>123 456 789</li>
        <li><svg viewBox="0 0 16 16"><path d="M0 3h16v10H0zm1.5 1.2V12h13V4.2L8 9z"/></svg>info@yourgmail.com</li>
        <li><svg viewBox="0 0 16 16"><circle cx="8" cy="8" r="8"/></svg>www.yourwebsite.com</li>
      </ul>

      <div class="person">
        <p class="person__name">MARCUS ELLERY</p>
        <p class="person__title">OWNER-CEO</p>
      </div>
      <span class="person-bar"></span>

      <div class="front-block"></div>
    </section>
  </main>
</body>
</html>
```